Leading Financial Advisory Firm Needs a Web Redesign

Job Type
Web Redesign

Task Outline
Create an Updated Web Design for our existing web site

Task Description
Dunmore Kestrel Group Inc. is a leading financial advisory firm to the global steel, metals and mining sectors. We are seeking a web designer to refashion, freshen and update the look of our existing website. The substance of the revised website should reflect our updated Credentials attached.

Our existing web site has an outdated “look”; it was originally put together quickly from an earlier PowerPoint presentation of our Credentials. We do not want the revised web site to look like a PowerPoint presentation which has been put up online. Rather, with a designer’s help, we would like to refashion the pages so that the look and feel of the site is consistent with a professional service organization's site. We are not interested in any significant changes in substance, just in format. There should also be no changes to the design/font/color of the “Dunmore Kestrel” logo.

The final selected designer will be responsible for all design and coding/programming responsibilities subject to our approval. The revised site should be done in Word Press or similar "user-friendly" application so that we can make edits afterwards.

A few specific changes:
• Textual changes:
• Wherever it currently says Dunmore Kestrel is an “affiliate” of Orvanne, this should be replaced with “Broker Dealer related services provided through Orvanne Partners LLC”; this appears on the copyright info on the bottom of each page;
• Please also add this telephone number to the 212 number listed: 917-555-0183;
• The text on the “About Us” tab needs to be updated as follows: “We currently have active steel, metals and mining assignments in Europe, South Africa, Australia and Ukraine.”
• The Services tab under Core Services currently says “Capital Raising (through affiliates)”; it should say “Capital Raising (through broker dealers)”;
• Our firm name in the Contacts tab should be “Dunmore Kestrel Group Inc.”
• Tara Wendle’ bio should be removed from the Bios tab;
• The map in the Global Scope and Perspective tab should be replaced with the map in the attached updated Credentials (see slide 11)

Very truly yours,

Dunmore Kestrel Group Inc.

Our current website is: http://www.dunmorekestrel.example

Deadline
5 Days

Target Market(s)
Companies in the steel, metals and mining sectors interested in financial advisory services and/or strategic and/or financial partners.

Industry/Entity Type

Financial

```html
<!DOCTYPE html>
<html lang="en">
<head>
<meta charset="utf-8">
<title>Dunmore Kestrel — Financial Advisors to Steel, Metals and Mining</title>
<link href="https://fonts.googleapis.com/css2?family=Open+Sans:wght@400;600&display=swap" rel="stylesheet">
<style>
:root{
  --green:#1f7a1f;
  --green-dark:#126012;
  --ink:#222;
  --text:#3a3a3a;
  --muted:#666;
  --frame:#e4e4e4;
  --footer-text:#b9b9b9;
  --footer-head:#d8d8d8;
  --white:#fff;
}
*{margin:0;padding:0;box-sizing:border-box}
html,body{width:709px;height:1200px;overflow:hidden}
body{position:relative;background:linear-gradient(#f3f3f3 0,#fafafa 360px,#fff 380px);font-family:"Open Sans",Arial,sans-serif;color:var(--text)}
.abs{position:absolute}
.brand-name{left:100px;top:24px;font-weight:600;font-size:15px;line-height:17px;color:var(--ink);letter-spacing:.4px}
.brand-tag{left:101px;top:42px;font-size:7px;line-height:9px;color:var(--muted);letter-spacing:.8px}
.contact-top{right:101px;top:22px;text-align:right;font-size:8.5px;color:#444;line-height:17px}
.contact-top svg{vertical-align:-1px;margin-right:6px}
.nav{left:101px;top:74px;width:507px;height:32px;display:flex;background:linear-gradient(#2a8c26,#136a14);border-radius:2px;box-shadow:0 1px 2px rgba(0,0,0,.25)}
.nav .home{width:45px;background:linear-gradient(#fff,#e9e9e9);display:flex;align-items:center;justify-content:center;border:1px solid #d6d6d6}
.nav a{color:var(--white);font-size:7.4px;font-weight:600;text-decoration:none;display:flex;align-items:center;padding:0 13px;border-right:1px solid rgba(0,0,0,.18);box-shadow:1px 0 0 rgba(255,255,255,.12)}
.nav a:first-of-type{padding-left:17px}
.hero{left:102px;top:123px;width:506px;height:226px;border:1px solid var(--frame);background:var(--white);padding:2px}
.hero .photo{width:100%;height:100%;background:radial-gradient(ellipse at 40% 75%,#fff6b8 0,#f6c23c 25%,#d38912 55%,#8a4a08 100%)}
.quote{left:228px;top:207px;width:276px;height:66px;background:rgba(70,75,60,.55);color:var(--white);font-size:12px;line-height:22px;text-align:center;padding-top:10px}
.arrow{width:16px;height:16px;border-radius:50%;background:rgba(255,255,255,.85);display:flex;align-items:center;justify-content:center}
.intro-title{left:101px;top:368px;font-size:14.5px;font-weight:400;color:var(--ink)}
.intro-tag{left:101px;top:388px;font-size:9.5px;color:var(--ink)}
.frame{border:1px solid var(--frame);background:var(--white);padding:2px}
.frame .photo{width:100%;height:100%}
.section-title{font-size:11.5px;font-weight:400;color:var(--ink)}
.copy{font-size:6.2px;line-height:11px;color:#333;text-align:justify}
.btn{left:102px;top:649px;width:57px;height:22px;background:var(--green);color:var(--white);font-size:7px;display:flex;align-items:center;justify-content:center;border-radius:2px}
.news-tag{position:absolute;left:3px;bottom:3px;background:var(--green);color:var(--white);font-size:8px;padding:0 5px;line-height:12px}
.news-title{font-size:8.4px;color:var(--ink)}
.news-by{font-size:5.6px;color:#444}
.news-copy{font-size:5.6px;line-height:11px;color:#444;width:145px;text-align:justify}
.read-more{left:578px;top:664px;font-size:6px;color:var(--green)}
.play{position:absolute;left:50%;top:50%;width:44px;height:44px;margin:-22px 0 0 -22px;border-radius:50%;background:rgba(40,40,40,.7);box-shadow:0 0 0 6px rgba(120,120,120,.3);display:flex;align-items:center;justify-content:center}
.partners-box{left:101px;top:928px;width:507px;height:53px;border:1px solid var(--frame);background:var(--white)}
.badge{position:absolute;top:12px;height:27px}
.round{position:absolute;top:944px;width:18px;height:18px;border-radius:50%;background:#333;display:flex;align-items:center;justify-content:center}
.footer{left:0;top:1007px;width:709px;height:193px;background:linear-gradient(#4d4d4d,#444)}
.f-head{font-size:8.6px;font-weight:400;color:var(--footer-head);letter-spacing:.3px}
.f-text{font-size:5.6px;line-height:11px;color:var(--footer-text)}
.f-item{font-size:6.6px;line-height:11px;color:var(--footer-text)}
.news-input{left:453px;width:112px;height:26px;background:var(--white);font-size:6px;color:#333;padding:10px 6px;line-height:7px}
.news-btn{left:565px;width:43px;height:26px;background:var(--green);color:var(--white);font-size:8.6px;display:flex;align-items:center;justify-content:center}
.f-rule{left:102px;width:506px;height:1px;background:#5a5a5a}
.f-small{font-size:5.6px;color:var(--footer-text)}
.social{width:12px;height:12px;border-radius:50%;background:#eee}
</style>
</head>
<body>

<header>
  <div class="abs brand-name">DUNMORE KESTREL</div>
  <div class="abs brand-tag">Experienced. Savvy. Relentless.</div>
  <div class="abs contact-top">
    <div><svg width="8" height="7" viewBox="0 0 8 7"><path d="M0 2 Q4 -1 8 2 L7 3 5 2.5 5 1.8 3 1.8 3 2.5 1 3Z M1.5 3.5h5l.8 3.5H.7Z" fill="#333"/></svg>Get In Touch</div>
    <div>Call : 917-555-0183</div>
  </div>
  <nav class="abs nav">
    <div class="home"><svg width="15" height="13" viewBox="0 0 15 13"><path d="M7.5 0 15 7h-2v6H9V9H6v4H2V7H0Z" fill="#111"/></svg></div>
    <a>About Us</a><a>Services</a><a>Epresentative Engagements</a><a>Global Scope And Perspective</a><a style="border:0;box-shadow:none">Contact &nbsp;Us</a>
  </nav>
</header>

<section>
  <div class="abs hero"><div class="photo" role="img" aria-label="Molten steel pouring with bright sparks in a mill"></div></div>
  <div class="abs quote">“One of the world’s premier financial advisors<br>to the steel, metals and mining industries.”</div>
  <div class="abs arrow" style="left:119px;top:234px"><svg width="6" height="7"><path d="M5 0 1 3.5 5 7" stroke="#888" fill="none" stroke-width="1.4"/></svg></div>
  <div class="abs arrow" style="left:572px;top:244px"><svg width="6" height="7"><path d="M1 0 5 3.5 1 7" stroke="#888" fill="none" stroke-width="1.4"/></svg></div>
</section>

<section>
  <h1 class="abs intro-title">DUNMORE KESTREL</h1>
  <div class="abs intro-tag">Experienced.&nbsp; Savvy.&nbsp; Relentless.</div>

  <div class="abs frame" style="left:102px;top:416px;width:239px;height:119px"><div class="photo" role="img" aria-label="Bank building facade viewed from below" style="background:linear-gradient(120deg,#2c3a2c,#8aa08e 45%,#c9d6cc 65%,#3f4f45)"></div></div>
  <h2 class="abs section-title" style="left:101px;top:553px">Representative Steel Engagements</h2>
  <p class="abs copy" style="left:102px;top:580px;width:239px">Lorem ipsum dolor sit amet, consectetur adipisicing elit, sed do eiusmod tempor incididunt ut labore et dolore magna. Lorem ipsum dolor sit amet, consectetur adipisicing elit, sed do eiusmod tempor incididunt ut labore et dolore magna.consectetur adipisicing elit, sed do eiusmod tempor incididunt ut labore et dolore magna.</p>
  <div class="abs btn">Learn More</div>

  <div class="abs frame" style="left:366px;top:416px;width:83px;height:62px"><div class="photo" role="img" aria-label="Business team standing together" style="background:linear-gradient(#e8eaec,#9aa0a6)"></div><span class="news-tag">News</span></div>
  <div class="abs news-title" style="left:463px;top:415px">Managing Partner of Alloy Partners</div>
  <div class="abs news-by" style="left:463px;top:437px">Helen R. Vosk</div>
  <p class="abs news-copy" style="left:463px;top:452px">One of the world's premier investment banks to the steel, metals, and mining industriesOne of the world's premier investment</p>

  <div class="abs frame" style="left:366px;top:502px;width:83px;height:62px"><div class="photo" role="img" aria-label="Businessman in an office" style="background:linear-gradient(#dfe3e6,#7e868c)"></div><span class="news-tag">News</span></div>
  <div class="abs news-title" style="left:463px;top:501px">Managing Partner of Alloy Partners</div>
  <div class="abs news-by" style="left:463px;top:523px">Helen R. Vosk</div>
  <p class="abs news-copy" style="left:463px;top:538px">One of the world's premier investment banks to the steel, metals, and mining industriesOne of the world's premier investment</p>

  <div class="abs frame" style="left:366px;top:590px;width:83px;height:62px"><div class="photo" role="img" aria-label="Portrait of a businessman" style="background:linear-gradient(#c9d8e2,#6f8796)"></div><span class="news-tag">News</span></div>
  <div class="abs news-title" style="left:463px;top:589px">Managing Partner of Alloy Partners</div>
  <div class="abs news-by" style="left:463px;top:611px">Helen R. Vosk</div>
  <p class="abs news-copy" style="left:463px;top:626px">One of the world's premier investment banks to the steel, metals, and mining industriesOne of the world's premier investment</p>
  <div class="abs read-more">Read More</div>
</section>

<section>
  <div class="abs frame" style="left:102px;top:696px;width:155px;height:107px"><div class="photo" role="img" aria-label="Compass pointing to the word strategy" style="background:linear-gradient(#efefe6,#bdbdaa)"></div><span class="play"><svg width="12" height="13"><path d="M0 0 12 6.5 0 13Z" fill="#2fae2f"/></svg></span></div>
  <div class="abs frame" style="left:277px;top:696px;width:155px;height:107px"><div class="photo" role="img" aria-label="File folders marked mergers and acquisitions" style="background:linear-gradient(#2a2a2a 20%,#d8d67a 55%,#e4e070)"></div><span class="play"><svg width="12" height="13"><path d="M0 0 12 6.5 0 13Z" fill="#2fae2f"/></svg></span></div>
  <div class="abs frame" style="left:452px;top:696px;width:156px;height:107px"><div class="photo" role="img" aria-label="Tablet and financial charts on a desk" style="background:linear-gradient(#f5f6f8,#c7ccd2)"></div><span class="play"><svg width="12" height="13"><path d="M0 0 12 6.5 0 13Z" fill="#2fae2f"/></svg></span></div>

  <h3 class="abs section-title" style="left:101px;top:815px;font-size:10px">Strategic&nbsp; Advice</h3>
  <h3 class="abs section-title" style="left:276px;top:815px;font-size:10px">Mergers &nbsp;&amp; Acquisitions</h3>
  <h3 class="abs section-title" style="left:452px;top:815px;font-size:10px">Capital Raising</h3>
  <p class="abs copy" style="left:102px;top:841px;width:155px">Dolor sit amet, consectetuer adipiscing elit, sed diam nonummy nibh euismod tincidunt ut laoreet dolore magna aliquam erat volutpat. Ut wisi enim ad minim veniam, quis nostrud exerci tation.</p>
  <p class="abs copy" style="left:277px;top:841px;width:155px">Dolor sit amet, consectetuer adipiscing elit, sed diam nonummy nibh euismod tincidunt ut laoreet dolore magna aliquam erat volutpat. Ut wisi enim ad minim veniam, quis nostrud exerci tation.</p>
  <p class="abs copy" style="left:452px;top:841px;width:155px">Dolor sit amet, consectetuer adipiscing elit, sed diam nonummy nibh euismod tincidunt ut laoreet dolore magna aliquam erat volutpat. Ut wisi enim ad minim veniam, quis nostrud exerci tation.</p>
</section>

<section>
  <h2 class="abs section-title" style="left:101px;top:904px;font-size:9.2px">Representative Steel Engagements</h2>
  <div class="abs partners-box">
    <div class="badge" style="left:23px;width:72px;background:linear-gradient(#eee,#c9c9c9)"></div>
    <div class="badge" style="left:110px;width:87px;background:#f2cc12"></div>
    <div class="badge" style="left:220px;width:87px;background:#f1f1f1"></div>
    <div class="badge" style="left:327px;width:82px;background:#d31a1a"></div>
    <div class="badge" style="left:425px;width:59px;background:#dedede"></div>
  </div>
  <div class="round" style="left:89px"><svg width="5" height="7"><path d="M4 0 1 3.5 4 7" stroke="#fff" fill="none" stroke-width="1.5"/></svg></div>
  <div class="round" style="left:603px"><svg width="5" height="7"><path d="M1 0 4 3.5 1 7" stroke="#fff" fill="none" stroke-width="1.5"/></svg></div>
</section>

<footer class="abs footer">
  <h4 class="abs f-head" style="left:102px;top:19px">DUNMORE KESTREL</h4>
  <p class="abs f-text" style="left:102px;top:45px;width:158px">Dunmore Kestrel is led by Robert M. Hale, Chairman and CEO, who has over 35 years of professional experience Mr. Hale is supported by a skilled professional staff Since its formation in 2003, Dunmore Kestrel has been widely recognized as the #1 independent financial advisor to the global steel, metals and mining sector We are international in scope, representing companies all around the world.</p>

  <h4 class="abs f-head" style="left:294px;top:18px">ADDRESS</h4>
  <svg class="abs" style="left:294px;top:45px" width="9" height="14" viewBox="0 0 9 14"><path d="M4.5 0A4.5 4.5 0 0 0 0 4.5C0 8 4.5 14 4.5 14S9 8 9 4.5A4.5 4.5 0 0 0 4.5 0Zm0 6.3a1.8 1.8 0 1 1 0-3.6 1.8 1.8 0 0 1 0 3.6Z" fill="#222"/></svg>
  <div class="abs f-item" style="left:313px;top:44px">Dunmore Kestrel &amp; Co., LLC<br>410 Harbor Avenue, 12th Floor<br>New York, NY 10099</div>
  <svg class="abs" style="left:295px;top:85px" width="9" height="15" viewBox="0 0 9 15"><rect width="9" height="15" rx="1.5" fill="#222"/><rect x="1.5" y="2" width="6" height="9" fill="#555"/></svg>
  <div class="abs f-item" style="left:315px;top:87px">Call us: (212) 555-0147</div>
  <svg class="abs" style="left:294px;top:121px" width="12" height="8" viewBox="0 0 12 8"><rect width="12" height="8" fill="#222"/><path d="M0 0 6 5 12 0" stroke="#777" fill="none" stroke-width=".8"/></svg>
  <div class="abs f-item" style="left:315px;top:119px">rhale@dunmorekestrel.example</div>

  <h4 class="abs f-head" style="left:453px;top:18px">NEWSLETTER</h4>
  <p class="abs f-text" style="left:453px;top:45px;width:155px">Excepteur sint occaecat cupidatat non proident, sunt in culpa qui officia deserunt mollit anim id est laborum.</p>
  <div class="abs news-input" style="top:87px">Enter Email</div>
  <div class="abs news-btn" style="top:87px">Sign Up</div>

  <div class="abs f-rule" style="top:144px"></div>
  <div class="abs f-small" style="left:102px;top:165px">Copyright © 2014 Dunmore Kestrel Group Inc . All rights reserved.</div>
  <div class="abs social" style="left:351px;top:161px"></div>
  <div class="abs social" style="left:368px;top:161px"></div>
  <div class="abs social" style="left:386px;top:161px"></div>
  <div class="abs social" style="left:404px;top:161px"></div>
  <div class="abs f-small" style="left:501px;top:165px">Home &nbsp;| &nbsp;About &nbsp;| &nbsp;Services &nbsp;| &nbsp;Contact</div>
</footer>

</body>
</html>
```